Brand Identity Stationary Package

Hello I'm looking for a full branding package for my Property Management Company. I have a logo but looking to have the following
Business Card
Email signature
Facebook cover photo
Letterhead (word.doc)
#10 Envelope
Pocket Folder - link to 9x12 pocket folder design specs https://www.printorbit-example.ca/marketing-materials/presentation-folders
would like everything to match and be brand identifiable. The company looks after residential properties/apartments and some commercial properties. Attached is a zip of the files.
For Business Card
Name: Gareth Lindqvist
Position: Operations Manager
Number: 1 (555) 384-2917
Email: Gareth@harborkey-example.ca
Website: Harborkey-example.ca
Property Management

```html
<!DOCTYPE html>
<html lang="en">
<head>
<meta charset="utf-8">
<title>Harborkey Letterhead</title>
<link href="https://fonts.googleapis.com/css2?family=Montserrat:wght@400;500;700;800&display=swap" rel="stylesheet">
<style>
  :root {
    --brand-green: #86ad3f;
    --ink: #1a1a1a;
    --paper: #ffffff;
    --backdrop: #ececed;
  }
  * { box-sizing: border-box; margin: 0; padding: 0; }
  html, body {
    width: 1200px; height: 874px; overflow: hidden;
    background: var(--backdrop);
    font-family: "Montserrat", sans-serif;
  }
  .canvas {
    width: 1200px; height: 874px;
    display: flex; align-items: center; justify-content: center;
  }
  .letterhead {
    position: relative;
    width: 580px; height: 820px;
    background: var(--paper);
    overflow: hidden;
  }
  .brand {
    position: absolute; left: 44px; top: 58px;
    color: var(--ink);
  }
  .brand-name {
    font-weight: 800; font-size: 34px; letter-spacing: 1px;
    line-height: 1;
  }
  .brand-tagline {
    margin-top: 6px;
    font-weight: 500; font-size: 9.5px; letter-spacing: 6.4px;
    text-transform: uppercase;
  }
  .contact {
    position: absolute; left: 372px; top: 40px;
    padding-left: 12px;
    border-left: 1px solid var(--brand-green);
    color: var(--ink);
    font-size: 9.5px; line-height: 1.45;
  }
  .contact-name {
    color: var(--brand-green); font-weight: 700;
    text-transform: uppercase; letter-spacing: 0.3px;
  }
  .contact-role { margin-bottom: 3px; }
  .contact-line { display: flex; align-items: center; gap: 7px; }
  .contact-line svg { width: 8px; height: 8px; fill: var(--brand-green); flex: none; }
  .footer-art {
    position: absolute; left: 0; bottom: 0;
    width: 580px; height: 400px;
    background: linear-gradient(160deg, rgba(255,255,255,0) 40%, rgba(134,173,63,0.55) 75%, var(--brand-green) 100%);
  }
</style>
</head>
<body>
<div class="canvas">
  <div class="letterhead">
    <div class="brand">
      <div class="brand-name">HARBORKEY</div>
      <div class="brand-tagline">Property Management</div>
    </div>

    <div class="contact">
      <div class="contact-name">Gareth Lindqvist</div>
      <div class="contact-role">Operations Manager</div>
      <div class="contact-line">
        <svg viewBox="0 0 10 10"><path d="M2 0.5 L3.6 0.5 L4.2 3 L3 3.8 Q4 6 6.2 7 L7 5.8 L9.5 6.4 L9.5 8 Q9.5 9.5 8 9.5 Q0.5 9 0.5 2 Q0.5 0.5 2 0.5Z"/></svg>
        <span>1 (555) 384-2917</span>
      </div>
      <div class="contact-line">
        <svg viewBox="0 0 10 10"><path d="M0.5 2 H9.5 V8 H0.5Z M0.5 2 L5 5.5 L9.5 2" fill="none" stroke="#86ad3f" stroke-width="1.2"/></svg>
        <span>Gareth@harborkey-example.ca</span>
      </div>
      <div class="contact-line">
        <svg viewBox="0 0 10 10"><circle cx="5" cy="5" r="4.5"/><path d="M0.5 5 H9.5 M5 0.5 Q2.5 5 5 9.5 M5 0.5 Q7.5 5 5 9.5" fill="none" stroke="#fff" stroke-width="0.7"/></svg>
        <span>Harborkey-example.ca</span>
      </div>
    </div>

    <div class="footer-art" role="img" aria-label="Decorative brand wave footer in green and black"></div>
  </div>
</div>
</body>
</html>
```